Powerpoint design template for LUMOTEX for new digital platform

We would like to use a PowerPoint template, we would like to create a new page, we would like to create a new digital platform LUMOTEX for schools and parents for the creation of playful communication and educational tools for children to enhance their positive development, amaze them learn in a playful way. This platform is going to be the most creative, stimulating and innovative classroom, easy to use and fast to implement. Scrapbooking, collages ... Magazine, newsletters Diplomla / awards Slideshows Facebook Calendars Organizers Greetings Games ... This powerpoint template will be used essential to We are looking for a professional design, positioning our brand in the children market with an adult hearing. so you will need to find a good deal. Primary target: nurseries & schools from 0 to 18 years old and universities (in 2nd phase) Secondary target: small & medium businesses Third target: general public, and TPE If it is a color scheme, then it is suggested that it be marketed in Europe (UK, Italy, Spain) and in a 2nd Stage USA and other countries. multiple options for front page, insidious pages (multiple styles with limited text and extended text) and final contact page We need something to read, we can not do it too much, but we can not do it. , and inside pages aligned to our logo

Target Market(s)

Target 1; Education with teacher Target 2; parents and grandparents

Industry/Entity Type

Education

Font styles to use
Other font styles liked:
• not decided. but not too fancy

Requirements
Must have
• Multi page options for front page, page insides (multiple styles with limited text and extended text) and final page contact
Nice to have
• do not have a lot of ideas. We need something to read, we can not get away from it
Should not have
• not too fancy and busy: keep clarity & simplicity while reassuring on quality

```html
<!DOCTYPE html>
<html lang="en">
<head>
<meta charset="utf-8">
<title>Lumotex – Section Slide</title>
<link href="https://fonts.googleapis.com/css2?family=Roboto+Condensed:wght@400;700&family=Hind:wght@400;600&family=Montserrat:wght@800&display=swap" rel="stylesheet">
<style>
  :root {
    --lime: #d9e03f;
    --lime-dark: #8cc63f;
    --lime-mid: #b5d334;
    --blue: #0aaeef;
    --blue-soft: #8fd8f7;
    --orange: #f47a1e;
    --orange-soft: #fbb78a;
    --green: #cfd92f;
    --green-soft: #e7ec98;
    --ink: #2b2b2b;
    --white: #ffffff;
  }
  * { margin: 0; padding: 0; box-sizing: border-box; }
  html, body { width: 1200px; height: 900px; overflow: hidden; background: var(--white); }
  .slide { position: relative; width: 1200px; height: 900px; overflow: hidden; background: var(--white); }

  .header-shape, .footer-shape { position: absolute; left: 0; display: block; }
  .header-shape { top: 0; }
  .footer-shape { top: 833px; }

  .project-title {
    position: absolute; left: 30px; top: 28px;
    font-family: "Roboto Condensed", "Arial Narrow", sans-serif;
    font-weight: 700; font-size: 46px; line-height: 1;
    color: var(--ink); letter-spacing: 0.5px;
  }

  .brand { position: absolute; left: 996px; top: 40px; }
  .brand-row { display: flex; align-items: center; gap: 10px; }
  .brand-mark { width: 20px; height: 20px; background: var(--lime-mid); }
  .brand-name {
    font-family: "Hind", sans-serif; font-weight: 600; font-size: 34px;
    line-height: 1; color: var(--ink); letter-spacing: 1px; padding-top: 6px;
  }
  .brand-tagline {
    margin: 6px 0 0 30px;
    font-family: "Hind", sans-serif; font-weight: 600; font-size: 10px;
    line-height: 1.2; color: var(--ink); letter-spacing: 2px;
  }

  .section {
    position: absolute; left: 0; width: 1200px;
    color: var(--white);
  }
  .section-blue { top: 138px; height: 222px; background: var(--blue); }
  .section-orange { top: 363px; height: 222px; background: var(--orange); }
  .section-green { top: 590px; height: 220px; background: var(--green); }

  .section-number {
    position: absolute; left: 16px; top: 8px;
    font-family: "Montserrat", sans-serif; font-weight: 800;
    font-size: 104px; line-height: 1.25;
  }
  .section-blue .section-number { color: var(--blue-soft); left: 26px; }
  .section-orange .section-number { color: var(--orange-soft); }
  .section-green .section-number { color: var(--green-soft); }

  .section-title {
    position: absolute; left: 116px; top: 18px;
    font-family: "Hind", sans-serif; font-weight: 600;
    font-size: 29px; line-height: 1.2;
  }
  .section-body {
    position: absolute; left: 116px; top: 64px; width: 950px;
    font-family: "Hind", sans-serif; font-weight: 400;
    font-size: 20px; line-height: 31.5px;
  }

  .site-url {
    position: absolute; left: 21px; top: 852px;
    font-family: "Roboto Condensed", "Arial Narrow", sans-serif;
    font-size: 23px; color: var(--ink);
  }
  .page-number {
    position: absolute; left: 1078px; top: 854px;
    font-family: "Roboto Condensed", "Arial Narrow", sans-serif;
    font-size: 21px; color: var(--ink);
  }
</style>
</head>
<body>
<div class="slide">

  <svg class="header-shape" width="1200" height="110" viewBox="0 0 1200 110" aria-hidden="true">
    <polygon points="930,0 990,0 945,95 900,108" fill="var(--lime-dark)"/>
    <polygon points="950,0 975,0 935,70" fill="var(--lime-mid)"/>
    <polygon points="0,0 955,0 900,108 0,108" fill="var(--lime)"/>
  </svg>

  <h1 class="project-title">PROJECT TITLE HERE</h1>

  <div class="brand">
    <div class="brand-row">
      <span class="brand-mark"></span>
      <span class="brand-name">LUMOTEX</span>
    </div>
    <p class="brand-tagline">YOUR TAGLINE<br>GOES HERE</p>
  </div>

  <section class="section section-blue">
    <span class="section-number">1</span>
    <h2 class="section-title">Section Title Here</h2>
    <p class="section-body">Lemon drops oat cake oat cake sugar plum sweet gingerbread chocolate cake<br>gingerbread. Lemon drops oat cake oat cake sugar plum sweet Lemon drops oat cake oat cake<br>sugar plum sweet gingerbread chocolate gingerbread. Lemon drops oat cake oat cake sugar<br>plum sweet</p>
  </section>

  <section class="section section-orange">
    <span class="section-number">2</span>
    <h2 class="section-title">Section Title Here</h2>
    <p class="section-body">Lemon drops oat cake oat cake sugar plum sweet gingerbread chocolate cake<br>gingerbread. Lemon drops oat cake oat cake sugar plum sweet Lemon drops oat cake oat cake<br>sugar plum sweet gingerbread chocolate gingerbread. Lemon drops oat cake oat cake sugar<br>plum sweet</p>
  </section>

  <section class="section section-green">
    <span class="section-number">3</span>
    <h2 class="section-title">Section Title Here</h2>
    <p class="section-body">Lemon drops oat cake oat cake sugar plum sweet gingerbread chocolate cake<br>gingerbread. Lemon drops oat cake oat cake sugar plum sweet Lemon drops oat cake oat cake<br>sugar plum sweet gingerbread chocolate gingerbread. Lemon drops oat cake oat cake sugar<br>plum sweet</p>
  </section>

  <svg class="footer-shape" width="1200" height="67" viewBox="0 0 1200 67" aria-hidden="true">
    <rect x="0" y="0" width="1200" height="67" fill="var(--lime)"/>
    <polygon points="975,0 1000,0 1040,67 1015,67" fill="var(--lime-dark)"/>
    <polygon points="990,0 1010,0 1030,40" fill="var(--lime-mid)"/>
    <polygon points="998,0 1200,0 1200,67 1050,67" fill="var(--orange)"/>
  </svg>

  <p class="site-url">www.lumotex.com</p>
  <p class="page-number">Page : 01</p>

</div>
</body>
</html>
```